Belvascotravel.com web design project + logo design

Hi,

We are a Russian online tour operator - sunkettle.com

We are looking to tranmsfer our domain to belvascotravel.com. The website and logo need to be belvascoesque - we are not looking to change our functionality, but we need to make the website much more attracitve to clients, much more wild looking but at the same time remaining a professional travel company.

The main concept of the website should be innovative travel (as belvasco was an innovator). Alternatively, you could go down the artist route and go down the draw / design your own tour road.

On our website the customer is able to combine travel services (hotels, flights, Visa services, and soon chauffeur, car rental etc...) put it into their basket (the basket definitely has to look better than it is at the moment) and pay for it in one go by card.

We are also stressin our customer support with web chat, call centre etc... (call centre number at the top of the page)

We aim to provide an easy user experience, but we need to make it have some more style, so I will be waiting for what you guys can come up with.
Let me know if you have any questions - skype is: mrdolbarin

Industry/Entity Type

It Company

Requirements
Must have
• It is quite a simple task - to take the existing website sunkettle.com and belvascosize it to create belvascotravel.com, the functionality of the website will remain the same and there are not many pages in the website. Homepage, Checkout step1, Checkout step 2 (you can view both of these if you select a service) and the generic pages for T&C''s, Privacy policy etc...

IMPORTANT UPDATE

We are also looking at how the search results will look in the designs, (please do a search on our website for hotel / flight)

```html
<!DOCTYPE html>
<html lang="ru">
<head>
<meta charset="utf-8">
<title>Belvasco Travel</title>
<link rel="stylesheet" href="https://fonts.googleapis.com/css2?family=PT+Serif&family=Ubuntu:wght@400;500;700&family=Arimo&display=swap">
<style>
:root{
  --paper:#efeadb;
  --paper-dark:#e4dcc6;
  --ink:#2b0d02;
  --brown:#2a0f05;
  --brown-soft:#3d2318;
  --rust:#6e2000;
  --rust-light:#7e2a06;
  --field:#ebe6d3;
  --text:#3a2418;
  --muted:#6b5a4c;
  --white:#ffffff;
}
*{box-sizing:border-box;margin:0;padding:0}
html,body{width:1200px;height:1067px;overflow:hidden}
body{position:relative;background:var(--paper);font-family:"Ubuntu",sans-serif;color:var(--text)}
.abs{position:absolute}

/* header */
.compass{left:-50px;top:-60px;width:178px;height:196px;border-radius:50%;background:radial-gradient(circle,#e9dcc0 0%,#d6c29c 55%,#9b5a2a 62%,#c7894f 70%,transparent 72%)}
.phone-icon{left:142px;top:55px}
.phones{left:197px;top:54px;font-family:"PT Serif",serif;font-size:14.5px;line-height:21px;color:var(--ink)}
.brand{left:500px;top:28px;width:200px;text-align:center;font-family:"PT Serif",serif;color:var(--ink)}
.brand-mark{display:block;width:10px;height:10px;background:var(--ink);margin:0 auto 8px;border-radius:50%}
.brand-name{font-size:31px;line-height:34px;display:block}
.brand-sub{font-size:12px;letter-spacing:5px;display:block;margin-top:6px}
.top-nav{right:74px;top:62px;display:flex;align-items:center;font-family:"PT Serif",serif;font-size:14px;color:var(--ink)}
.top-nav a{display:flex;align-items:center;gap:10px;color:inherit;text-decoration:none}
.top-nav .sep{width:0;height:24px;border-left:1px dashed #b8aa90;margin:0 22px}

/* hero */
.hero{left:0;top:152px;width:1200px;height:257px;background:linear-gradient(180deg,#c8b89a 0%,#a58f6e 35%,#4d4d68 70%,#2e2f4a 100%)}
.tabs{left:317px;top:377px;display:flex;gap:8px}
.tab{width:183px;height:32px;background:var(--brown);color:var(--white);display:flex;align-items:center;justify-content:center;gap:10px;font-size:14px;border-radius:3px 3px 0 0}
.tab.active{background:var(--rust)}

/* ticket & map decor */
.ticket{left:-40px;top:480px;width:190px;height:230px;background:linear-gradient(160deg,#e8e0cc,#d5c9ad);transform:rotate(-28deg);box-shadow:0 4px 10px rgba(0,0,0,.2)}
.map{left:430px;top:935px;width:250px;height:170px;background:linear-gradient(135deg,#e9dfc4,#c9b895 60%,#a4977a);transform:rotate(14deg);box-shadow:0 3px 8px rgba(0,0,0,.2)}

/* search panel */
.search{left:155px;top:409px;width:890px;height:259px;background:var(--white)}
.label{position:absolute;font-size:13.5px;font-weight:500;color:var(--ink)}
.field{position:absolute;height:37px;background:var(--field);font-size:13.5px;color:#4a3a30;display:flex;align-items:center;padding-left:14px}
.field svg{margin-right:12px}
.spin{width:90px;padding-left:20px;font-size:15px}
.spin .arrows{position:absolute;right:0;top:0;width:30px;height:37px;border-left:1px solid #fff;display:flex;flex-direction:column;align-items:center;justify-content:center;gap:7px}
.select .caret{position:absolute;right:0;top:0;width:30px;height:37px;border-left:1px solid #cfc7b0;display:flex;align-items:center;justify-content:center}
.check{position:absolute;display:flex;align-items:center;gap:10px;font-size:12px;color:#4a3a30}
.box{width:16px;height:16px;background:var(--brown);border-radius:3px;display:flex;align-items:center;justify-content:center}
.btn-search{position:absolute;left:726px;top:200px;width:139px;height:35px;background:var(--rust);color:var(--white);border-radius:3px;font-size:14px;display:flex;align-items:center;justify-content:center}

/* basket */
.basket{left:155px;top:668px;width:890px;height:97px;background:var(--brown)}
.basket-zig{left:155px;top:663px}
.basket-title{position:absolute;left:23px;top:23px;display:flex;align-items:center;gap:18px;font-family:"PT Serif",serif;font-size:15px;color:#e9dfcd;letter-spacing:.5px}
.scroll-btn{position:absolute;top:16px;width:11px;height:66px;background:#5a4234;display:flex;align-items:center;justify-content:center}
.item{position:absolute;top:16px;width:181px;height:66px;background:var(--brown-soft);color:#e9dfcd;font-size:12px}
.item .row{position:absolute;left:12px;display:flex;align-items:center;gap:10px}
.item b{font-weight:700;font-size:13.5px;margin-left:4px}
.item .x{position:absolute;right:8px;bottom:8px}
.total{position:absolute;left:651px;top:30px;color:#e9dfcd;font-size:11px}
.total strong{display:block;font-size:19px;margin-top:4px}
.total strong span{font-size:12px;font-weight:400;margin-left:4px}
.pay{position:absolute;right:0;top:0;width:121px;height:97px;background:var(--rust);color:var(--white);font-weight:700;font-size:15px;display:flex;align-items:center;justify-content:center;letter-spacing:.5px}

/* footer */
.col{position:absolute;top:806px}
.col h3{font-family:"PT Serif",serif;font-weight:400;font-size:15px;color:var(--ink);margin-bottom:18px;letter-spacing:.3px}
.col ul{list-style:none;font-family:"Arimo",sans-serif;font-size:11.5px;line-height:20.5px;color:var(--ink)}
.socials{position:absolute;left:785px;top:834px;display:flex;gap:11px}
.socials span{width:44px;height:44px;border-radius:50%;background:#e2d3ac;box-shadow:inset 0 0 0 3px #d2bf92}
.contacts{position:absolute;left:787px;top:896px;list-style:none;font-family:"Arimo",sans-serif;font-size:11.5px;color:var(--ink)}
.contacts li{display:flex;align-items:center;gap:10px;height:24px}
.subscribe{position:absolute;left:788px;top:980px;display:flex;gap:5px}
.subscribe .input{width:185px;height:26px;background:#ddd6b8;border:1px solid #cfc7a8;font-family:"Arimo",sans-serif;font-size:11px;color:#6b5a4c;padding:6px 10px}
.subscribe .send{width:76px;height:26px;background:var(--brown);color:var(--white);font-family:"Arimo",sans-serif;font-size:11.5px;display:flex;align-items:center;justify-content:center}
.copy{left:142px;top:988px;font-family:"Arimo",sans-serif;font-size:13px;color:var(--ink)}
</style>
</head>
<body>

<header>
  <div class="abs compass" role="img" aria-label="Старинный компас"></div>
  <svg class="abs phone-icon" width="38" height="38" viewBox="0 0 38 38" aria-hidden="true">
    <path d="M3 12c0-6 32-6 32 0v4h-8v-4c-4-2-12-2-16 0v4H3z" fill="#2b0d02"/>
    <path d="M10 17h18l5 16H5z" fill="#2b0d02"/>
    <circle cx="19" cy="25" r="5" fill="#efeadb"/><circle cx="19" cy="25" r="2" fill="#2b0d02"/>
  </svg>
  <div class="abs phones">+8 (800) 5551420<br>+7 (495) 5550187</div>

  <div class="abs brand">
    <span class="brand-mark"></span>
    <span class="brand-name">Belvasco</span>
    <span class="brand-sub">TRAVEL</span>
  </div>

  <nav class="abs top-nav">
    <a href="#"><svg width="26" height="24" viewBox="0 0 26 24"><path d="M13 1C6 1 1 5.5 1 11c0 3 1.5 5.5 4 7.5L4 23l6-3c1 .2 2 .3 3 .3 7 0 12-4.5 12-10S20 1 13 1z" fill="#2b0d02"/><text x="8" y="15" font-size="11" fill="#efeadb" font-family="serif">”</text></svg>ФОРУМ</a>
    <span class="sep"></span>
    <a href="#"><svg width="26" height="24" viewBox="0 0 26 24"><circle cx="16" cy="3" r="2.5" fill="#2b0d02"/><path d="M14 6l-5 6 3 2-5 9h3l5-8 3 3v5h3v-7l-4-4 2-3 3 3h3l-5-6z" fill="#2b0d02"/><rect x="1" y="10" width="7" height="9" fill="#2b0d02"/></svg>МОЙ ТУР</a>
  </nav>
</header>

<div class="abs hero" role="img" aria-label="Фото: набережная Сены, собор и мост в Париже"></div>

<div class="abs tabs">
  <div class="tab active"><svg width="28" height="14" viewBox="0 0 28 14"><path d="M0 0h28v5a2 2 0 000 4v5H0V9a2 2 0 000-4z" fill="#fff"/><path d="M12 4l2 2 3-1-2 2 1 3-2-2-3 2 1-3-2-1h2z" fill="#6e2000"/></svg>АВИАБИЛЕТИ</div>
  <div class="tab"><svg width="18" height="18" viewBox="0 0 18 18"><rect x="1" y="1" width="16" height="16" fill="none" stroke="#fff" stroke-width="2" stroke-dasharray="2 1"/><circle cx="9" cy="7" r="2.5" fill="#fff"/><path d="M4 14c1-3 9-3 10 0z" fill="#fff"/></svg>ВИЗЫ</div>
  <div class="tab"><svg width="30" height="18" viewBox="0 0 30 18"><rect x="0" y="1" width="3" height="17" fill="#fff"/><rect x="0" y="10" width="30" height="4" fill="#fff"/><rect x="27" y="6" width="3" height="12" fill="#fff"/><rect x="5" y="5" width="6" height="4" fill="#fff"/><rect x="12" y="5" width="14" height="4" fill="#fff"/></svg>ОТЕЛИ</div>
</div>

<div class="abs ticket" role="img" aria-label="Посадочный талон"></div>

<section class="abs search">
  <span class="label" style="left:25px;top:27px">Откуда</span>
  <span class="label" style="left:294px;top:27px">Куда</span>
  <span class="label" style="left:558px;top:27px">Взрослый</span>
  <span class="label" style="left:670px;top:27px">Дети</span>
  <span class="label" style="left:777px;top:27px">Младенец</span>

  <div class="field" style="left:25px;top:42px;width:247px">Москва, Россия (All Airports)</div>
  <div class="field" style="left:291px;top:42px;width:248px">Прага, Чехия (All Airports)</div>
  <div class="field spin" style="left:557px;top:42px">2<span class="arrows"><svg width="9" height="5"><path d="M0 5L4.5 0 9 5z" fill="#2b0d02"/></svg><svg width="9" height="5"><path d="M0 0l4.5 5L9 0z" fill="#2b0d02"/></svg></span></div>
  <div class="field spin" style="left:666px;top:42px">2<span class="arrows"><svg width="9" height="5"><path d="M0 5L4.5 0 9 5z" fill="#2b0d02"/></svg><svg width="9" height="5"><path d="M0 0l4.5 5L9 0z" fill="#2b0d02"/></svg></span></div>
  <div class="field spin" style="left:775px;top:42px">2<span class="arrows"><svg width="9" height="5"><path d="M0 5L4.5 0 9 5z" fill="#2b0d02"/></svg><svg width="9" height="5"><path d="M0 0l4.5 5L9 0z" fill="#2b0d02"/></svg></span></div>

  <span class="label" style="left:25px;top:107px">Туда</span>
  <span class="label" style="left:297px;top:107px">Обратно</span>
  <div class="field" style="left:25px;top:122px;width:247px"><svg width="12" height="12" viewBox="0 0 12 12"><rect x="0.5" y="1.5" width="11" height="10" fill="none" stroke="#3a2418"/><rect x="0.5" y="1.5" width="11" height="3" fill="#3a2418"/><path d="M3 7h2M7 7h2M3 9h2M7 9h2" stroke="#3a2418"/></svg>12 Мая 2013</div>
  <div class="field" style="left:295px;top:122px;width:247px"><svg width="12" height="12" viewBox="0 0 12 12"><rect x="0.5" y="1.5" width="11" height="10" fill="none" stroke="#3a2418"/><rect x="0.5" y="1.5" width="11" height="3" fill="#3a2418"/><path d="M3 7h2M7 7h2M3 9h2M7 9h2" stroke="#3a2418"/></svg>12 Июня 2013</div>
  <div class="check" style="left:567px;top:132px"><span class="box"><svg width="10" height="8"><path d="M1 4l3 3 5-6" stroke="#fff" stroke-width="1.8" fill="none"/></svg></span>Обратно</div>
  <div class="check" style="left:666px;top:132px"><span class="box"></span>В одну сторону</div>

  <span class="label" style="left:25px;top:186px">Класс</span>
  <div class="field select" style="left:25px;top:201px;width:247px">Эконом<span class="caret"><svg width="10" height="6"><path d="M0 0l5 6 5-6z" fill="#2b0d02"/></svg></span></div>
  <div class="btn-search">ПОИСК</div>
</section>

<svg class="abs basket-zig" width="890" height="6" aria-hidden="true"><defs><pattern id="zig" width="8" height="6" patternUnits="userSpaceOnUse"><path d="M0 6L4 1 8 6z" fill="#2a0f05"/></pattern></defs><rect width="890" height="6" fill="url(#zig)"/></svg>
<section class="abs basket">
  <div class="basket-title"><svg width="28" height="38" viewBox="0 0 28 38"><path d="M8 12V7a6 6 0 0112 0v5" stroke="#6e2000" stroke-width="2.5" fill="none"/><rect x="0" y="11" width="28" height="27" fill="#6e2000"/><circle cx="14" cy="24" r="2" fill="#2a0f05"/></svg>КОРЗИНА</div>
  <div class="scroll-btn" style="left:158px"><svg width="5" height="10"><path d="M5 0L0 5l5 5z" fill="#2a0f05"/></svg></div>
  <div class="item" style="left:173px">
    <div class="row" style="top:14px"><svg width="20" height="10"><path d="M0 0h20v3a2 2 0 000 4v3H0V7a2 2 0 000-4z" fill="#c9bba5"/></svg>Мос - Прг <b>12349 Руб</b></div>
    <div class="row" style="top:40px"><svg width="10" height="18" style="margin:0 5px"><circle cx="5" cy="3" r="2.5" fill="#c9bba5"/><rect x="2" y="6" width="6" height="12" fill="#c9bba5"/></svg>2 Взрослый</div>
    <svg class="x" width="11" height="11"><path d="M0 0l11 11M11 0L0 11" stroke="#8d7c6c"/></svg>
  </div>
  <div class="item" style="left:363px">
    <div class="row" style="top:14px"><svg width="20" height="10"><path d="M0 0h20v3a2 2 0 000 4v3H0V7a2 2 0 000-4z" fill="#c9bba5"/></svg>Мос - Прг <b>12349 Руб</b></div>
    <div class="row" style="top:40px"><svg width="10" height="18" style="margin:0 5px"><circle cx="5" cy="3" r="2.5" fill="#c9bba5"/><rect x="2" y="6" width="6" height="12" fill="#c9bba5"/></svg>2 Взрослый</div>
    <svg class="x" width="11" height="11"><path d="M0 0l11 11M11 0L0 11" stroke="#8d7c6c"/></svg>
  </div>
  <div class="scroll-btn" style="left:623px"><svg width="5" height="10"><path d="M0 0l5 5-5 5z" fill="#2a0f05"/></svg></div>
  <div class="total">Итого :<strong>17149<span>Руб</span></strong></div>
  <div class="pay">ОПЛАТА</div>
</section>

<div class="abs map" role="img" aria-label="Старинная карта Европы"></div>

<footer>
  <div class="col" style="left:142px"><h3>ПРОСМОТР САЙТА</h3><ul><li>Домой</li><li>О нас</li><li>Форум</li><li>Контакты</li></ul></div>
  <div class="col" style="left:349px"><h3>ПОМОЩЬ</h3><ul><li>Помощь</li><li>Правила пользования</li><li>Политика конфиденциальности</li><li>Cookies</li></ul></div>
  <div class="col" style="left:589px"><h3>НАЙТИ НАС</h3><ul><li>Sunkettle Limited</li><li>14 Harrow Lane</li><li>London, E2 7QX</li><li>UK</li></ul></div>
  <div class="col" style="left:790px"><h3>МЫ В</h3></div>
  <div class="socials"><span role="img" aria-label="Соцсеть 1"></span><span role="img" aria-label="Соцсеть 2"></span><span role="img" aria-label="Соцсеть 3"></span></div>
  <ul class="contacts">
    <li><svg width="15" height="12" viewBox="0 0 15 12"><path d="M1 4c0-3 13-3 13 0v1h-3V4c-2-1-5-1-7 0v1H1z" fill="#2b0d02"/><path d="M4 5h7l2 7H2z" fill="#2b0d02"/></svg>+7 (495) 555-01-87</li>
    <li><svg width="15" height="11" viewBox="0 0 15 11"><rect x="0.5" y="0.5" width="14" height="10" fill="none" stroke="#2b0d02"/><path d="M0.5 0.5l7 6 7-6" fill="none" stroke="#2b0d02"/></svg>info@sunkettle.com</li>
    <li><svg width="15" height="13" viewBox="0 0 15 13"><circle cx="2" cy="11" r="2" fill="#2b0d02"/><path d="M1 5a7 7 0 017 7M1 1a11 11 0 0111 11" stroke="#2b0d02" stroke-width="2" fill="none"/></svg>Эксклюзивные предложения</li>
  </ul>
  <div class="subscribe"><div class="input">E- mail</div><div class="send">Отправить</div></div>
  <div class="abs copy">2013 © Sunkettle.com</div>
</footer>

</body>
</html>
```